New website for engineering consultant

We need to update our existing web site. We've just had our logo re-done and have attached it.

We are an engineering consulting firm that specialises in mechanical and structural engineering, design and drafting. Our customers are other businesses in the manufacturing, mining and agricultural industries.

We would like the designs to be professional and highlight that we are innovative.

Industry/Entity Type

Mining

Requirements
Must have
• A module that rotates pictures so we can showcase certain projects. We have attached a few rendered images of projects for you to play with.

```html
<!DOCTYPE html>
<html lang="en">
<head>
<meta charset="utf-8">
<title>TORVEX — Mechanical Engineering</title>
<link href="https://fonts.googleapis.com/css2?family=Ubuntu:wght@400;500&display=swap" rel="stylesheet">
<style>
:root{
  --bg-deep:#010a3a;
  --bg-glow:#0b4bb8;
  --panel-edge:#1e4ea8;
  --card-edge:#2657b0;
  --header:#f4f4f4;
  --brand:#1330a8;
  --nav:#0d2f8c;
  --nav-arrow:#3a8fe0;
  --text:#e4ebf7;
  --link:#1a6cff;
  --tab:#1ea2ea;
  --tab-dark:#0b6fc2;
  --green-head:#c9f5c0;
  --render-hi:#e2e23a;
  --render-mid:#9fa832;
}
*{box-sizing:border-box;margin:0;padding:0}
html,body{width:1200px;height:1125px;overflow:hidden}
body{
  font-family:"Ubuntu",sans-serif;
  background:radial-gradient(ellipse 70% 55% at 50% 30%,var(--bg-glow),#06268a 45%,var(--bg-deep) 100%);
  position:relative;color:var(--text);
}
.site-header{position:absolute;left:18px;top:17px;width:1164px;height:135px;background:var(--header)}
.brand{position:absolute;left:18px;top:12px;width:415px;height:110px;background:#fff;border-radius:14px;display:flex;align-items:center;padding-left:22px;gap:16px}
.brand-mark{width:54px;height:54px;border-radius:50%;background:var(--brand);flex:none}
.brand-name{font-size:34px;font-weight:500;color:var(--brand);letter-spacing:.5px}
.main-nav{position:absolute;left:664px;top:28px;display:flex}
.main-nav a{display:flex;align-items:center;gap:8px;color:var(--nav);text-decoration:none;font-size:15px;margin-right:40px}
.main-nav a:last-child{margin-right:0}
.search{position:absolute;left:834px;top:77px;width:277px;height:35px;border:1px solid #8fb4dc;border-radius:18px;background:#fff;box-shadow:inset 0 1px 3px rgba(0,0,0,.15);display:flex;align-items:center;padding:0 14px 0 16px;font-size:14px;color:#555;justify-content:space-between}
.slider-image{position:absolute;left:360px;top:200px;width:440px;height:250px;border-radius:20px;background:radial-gradient(ellipse 60% 55% at 50% 50%,var(--render-hi),var(--render-mid) 45%,rgba(11,75,184,0) 100%)}
.slider-arrow{position:absolute;width:46px;height:46px;border-radius:50%;background:radial-gradient(circle at 40% 30%,#6fb8ea,#1b6db8 70%);box-shadow:0 2px 6px rgba(0,0,0,.4);display:flex;align-items:center;justify-content:center}
.slider-arrow.prev{left:135px;top:368px}
.slider-arrow.next{left:1001px;top:379px}
.showcase-tab{position:absolute;left:917px;top:450px;width:229px;height:90px;background:linear-gradient(180deg,var(--tab),var(--tab-dark));clip-path:polygon(0 0,100% 8%,97% 92%,0 100%);display:flex;align-items:center;padding-left:14px;gap:18px;font-size:18px;font-weight:500;color:#fff;z-index:2}
.showcase-tab .btn{width:46px;height:46px;border-radius:50%;background:radial-gradient(circle at 40% 30%,#5fb0e6,#0c4e94);display:flex;align-items:center;justify-content:center}
.welcome{position:absolute;left:42px;top:497px;width:1115px;height:469px;background:linear-gradient(180deg,rgba(16,52,130,.85),rgba(8,30,90,.9));border:2px solid var(--panel-edge);border-radius:18px;padding:22px 20px}
.welcome h1{font-size:24px;font-weight:400;color:#fff;margin-bottom:14px}
.welcome p{font-size:14px;line-height:17.4px;margin-bottom:17px;letter-spacing:.3px;padding-right:18px}
.services{position:absolute;left:114px;top:222px}
.service{position:absolute;top:0;width:264px;height:225px;border:1px solid var(--card-edge);border-radius:14px;background:linear-gradient(180deg,#0f3382,#081f62)}
.service h2{position:absolute;font-size:15px;font-weight:400;color:#fff;white-space:nowrap}
.service .art{position:absolute;border-radius:10px}
.service p{position:absolute;left:16px;right:14px;font-size:12px;line-height:15px}
.service a{position:absolute;right:28px;font-size:12px;color:var(--link);text-decoration:none}
.site-footer{position:absolute;left:58px;top:1010px;width:1103px;height:76px;border-radius:16px;background:linear-gradient(180deg,#123a8c,#0a2466);display:flex;align-items:center;justify-content:space-between;padding:0 58px 0 30px;font-size:12px;color:#fff}
.social{display:flex;gap:16px}
.social span{width:33px;height:33px;border-radius:3px;display:block}
</style>
</head>
<body>
<header class="site-header">
  <div class="brand"><span class="brand-mark"></span><span class="brand-name">TORVEX</span></div>
  <nav class="main-nav">
    <a href="#"><svg width="16" height="14" viewBox="0 0 16 14"><path d="M2 1v7h9" fill="none" stroke="var(--nav-arrow)" stroke-width="3"/><path d="M10 3l5 5-5 5z" fill="var(--nav-arrow)"/></svg>Home</a>
    <a href="#"><svg width="16" height="14" viewBox="0 0 16 14"><path d="M2 1v7h9" fill="none" stroke="var(--nav-arrow)" stroke-width="3"/><path d="M10 3l5 5-5 5z" fill="var(--nav-arrow)"/></svg>About Us</a>
    <a href="#"><svg width="16" height="14" viewBox="0 0 16 14"><path d="M2 1v7h9" fill="none" stroke="var(--nav-arrow)" stroke-width="3"/><path d="M10 3l5 5-5 5z" fill="var(--nav-arrow)"/></svg>Projects</a>
    <a href="#"><svg width="16" height="14" viewBox="0 0 16 14"><path d="M2 1v7h9" fill="none" stroke="var(--nav-arrow)" stroke-width="3"/><path d="M10 3l5 5-5 5z" fill="var(--nav-arrow)"/></svg>Contact Us</a>
  </nav>
  <div class="search"><span>This is my new search</span><svg width="20" height="20" viewBox="0 0 20 20"><circle cx="8" cy="8" r="6" fill="none" stroke="#9aa" stroke-width="2.5"/><path d="M12.5 12.5l6 6" stroke="#9aa" stroke-width="3" stroke-linecap="round"/></svg></div>
</header>

<div class="slider-image" role="img" aria-label="Rendered image of a featured engineering project in the showcase slider"></div>
<div class="slider-arrow prev"><svg width="16" height="18" viewBox="0 0 16 18"><path d="M11 2L4 9l7 7" fill="none" stroke="#fff" stroke-width="3.5"/></svg></div>
<div class="slider-arrow next"><svg width="16" height="18" viewBox="0 0 16 18"><path d="M5 2l7 7-7 7" fill="none" stroke="#fff" stroke-width="3.5"/></svg></div>
<div class="showcase-tab"><span class="btn"><svg width="16" height="18" viewBox="0 0 16 18"><path d="M5 2l7 7-7 7" fill="none" stroke="#fff" stroke-width="3.5"/></svg></span>Our showcase</div>

<main class="welcome">
  <h1>Welcome</h1>
  <p>TORVEX is a mechanical engineering and technology company focused on helping local&nbsp; manufacturing companies and local industries improve their products, services and sustainability through the application of engineering, technology and focused improvement.</p>
  <p>We offer a broad range of services that are designed to support and nurture manufacturing companies and industries whether you are big or small. We bring togther the services you would only find in a capital city to companies in North Queensland at a competitive rates. Our core services revolve around the application of the latest 3D Solid Modelling technology to assist in creating solutions to your mechanical design problems. These services are complemented by our Technology services which are designed to help your company leverage the latest technology to become globally competitive. Furthermore we offer a range of Focused Im-provement and Specialty services as we strive to bring you complete solutions to your business.</p>
  <div class="services">
    <article class="service" style="left:0">
      <div class="art" role="img" aria-label="Drafting compass over a blueprint" style="left:18px;top:6px;width:70px;height:100px;background:linear-gradient(160deg,#cfe4f7,#5c8fc4)"></div>
      <h2 style="left:97px;top:20px">Engineering &amp; Design</h2>
      <p style="top:128px">We offer a broad range of services that are designed to support and nurture manufacturing companies and industries whether you are big or small. We bring togther the services</p>
      <a href="#" style="top:204px">Read More</a>
    </article>
    <article class="service" style="left:299px">
      <div class="art" role="img" aria-label="Specialist consultant figure" style="left:18px;top:10px;width:78px;height:115px;background:linear-gradient(180deg,#e6ecf2,#7d8ea4)"></div>
      <h2 style="left:105px;top:23px;color:var(--green-head)">Speciality Services</h2>
      <p style="top:128px">We offer a broad range of services that are designed to support and nurture manufacturing companies and industries whether you are big or small. We bring togther the services</p>
      <a href="#" style="top:204px">Read More</a>
    </article>
    <article class="service" style="left:604px">
      <h2 style="left:16px;top:27px">Technology</h2>
      <div class="art" role="img" aria-label="Computer monitor" style="left:160px;top:16px;width:90px;height:80px;background:linear-gradient(150deg,#d8e6f4,#2d6cc0 60%,#9fb4c9)"></div>
      <p style="top:124px">We offer a broad range of services that are designed to support and nurture manufacturing companies and industries whether you are big or small. We bring togther the services</p>
      <a href="#" style="top:199px">Read More</a>
    </article>
  </div>
</main>

<footer class="site-footer">
  <span>Copyright © 2009 TORVEX PTY LTD &nbsp;&nbsp;&nbsp; All Rights Reserved.</span>
  <div class="social">
    <span style="background:#3b5ba6"></span>
    <span style="background:#3aa7dc"></span>
    <span style="background:#1f7fc2"></span>
    <span style="background:#e9e9e9"></span>
  </div>
</footer>
</body>
</html>
```